Business Card Design

REALTOR, QLMS
I want lock and key and possibly tiffany blue color

Industry/Entity Type

Business

Contact Information for Business Card

Dana Whitlow
NESTORA Pine
4817 W Falcon Drive Unit 12, Lodi, CA 95240
Cell 209-555-0148
Fax 209-555-0172
BRE# 01956027
danalistshomes@quillpost.com
www.danalistshomes.com

```html
<!DOCTYPE html>
<html lang="en">
<head>
<meta charset="utf-8">
<title>Dana Whitlow – Business Card</title>
<link rel="stylesheet" href="https://fonts.googleapis.com/css2?family=Playfair+Display:wght@700&family=Didact+Gothic&family=Arimo:wght@700&display=swap">
<style>
  :root {
    --page: #e7ecee;
    --tiffany: #3dbdb8;
    --tiffany-deep: #2fb0ab;
    --tiffany-light: #5ccac5;
    --name-grey: #dcdcdc;
    --white: #ffffff;
    --ink: #3b4a4a;
    --rule: rgba(255,255,255,0.55);
  }
  * { margin: 0; padding: 0; box-sizing: border-box; }
  html, body { width: 1200px; height: 960px; overflow: hidden; }
  body {
    background: var(--page);
    font-family: "Didact Gothic", sans-serif;
    position: relative;
  }
  .card {
    position: absolute;
    left: 250px;
    width: 700px;
    height: 400px;
    background: var(--tiffany);
    overflow: hidden;
    box-shadow: 0 6px 18px rgba(0,0,0,0.18);
  }
  .card--front { top: 50px; }
  .card--back { top: 500px; }

  .card__lines { position: absolute; inset: 0; }

  /* front */
  .identity {
    position: absolute; left: 70px; top: 40px;
    display: inline-flex; flex-direction: column; align-items: flex-end;
  }
  .agent-name {
    font-family: "Playfair Display", serif; font-weight: 700;
    font-size: 40px; line-height: 1.1; color: var(--name-grey); letter-spacing: 0.5px;
  }
  .brokerage {
    font-size: 21px; line-height: 1.1; color: var(--white); margin-top: 2px;
  }
  .headline-rule {
    position: absolute; left: 380px; top: 66px; width: 290px; height: 3px;
    background: linear-gradient(90deg, rgba(255,255,255,0), rgba(255,255,255,0.7));
  }
  .contacts { position: absolute; left: 382px; top: 138px; list-style: none; }
  .contacts__item {
    display: flex; align-items: center; height: 40px;
    font-size: 14px; color: var(--white);
  }
  .contacts__icon { width: 28px; display: flex; justify-content: center; margin-right: 14px; }
  .contacts__icon svg { display: block; }
  .contacts__label { width: 28px; margin-right: 14px; font-size: 13px; color: var(--rule); }
  .contacts__text { border-bottom: 1px solid var(--rule); padding: 0 8px 5px 0; }
  .contacts__text--small { font-size: 12px; }
  .agent-photo {
    position: absolute; left: 100px; top: 196px; width: 150px; height: 154px;
    background: linear-gradient(180deg, #c9a778 0%, #2b2b30 55%, #1d1d22 100%);
  }
  .website-front {
    position: absolute; left: 92px; top: 362px;
    font-size: 17px; color: var(--white); letter-spacing: 0.3px;
  }

  /* back */
  .keychain-art {
    position: absolute; left: 120px; top: 40px; width: 460px; height: 300px;
    background: radial-gradient(ellipse at center, rgba(150,220,215,0.55), rgba(150,220,215,0.15) 70%, rgba(150,220,215,0) 100%);
  }
  .tagline {
    position: absolute; left: 60px; top: 142px;
    font-size: 31px; line-height: 36px; color: var(--white); letter-spacing: 1.5px;
  }
  .website-back {
    position: absolute; left: 168px; top: 212px;
    font-family: "Arimo", sans-serif; font-weight: 700;
    font-size: 22px; line-height: 26px; color: var(--ink); letter-spacing: 1px;
  }
</style>
</head>
<body>

<section class="card card--front" aria-label="Business card front">
  <svg class="card__lines" width="700" height="400" viewBox="0 0 700 400" aria-hidden="true">
    <rect x="0" y="350" width="700" height="50" fill="var(--tiffany-deep)" opacity="0.35"/>
    <path d="M0 350 H300 L314 336 H420 L434 350 H700" fill="none" stroke="var(--tiffany-light)" stroke-width="2"/>
    <line x1="0" y1="392" x2="700" y2="392" stroke="var(--tiffany-light)" stroke-width="1.5"/>
  </svg>
  <div class="identity">
    <div class="agent-name">Dana Whitlow</div>
    <div class="brokerage">NESTORA Pine</div>
  </div>
  <div class="headline-rule"></div>

  <ul class="contacts">
    <li class="contacts__item">
      <span class="contacts__icon">
        <svg width="16" height="16" viewBox="0 0 24 24"><path d="M6.6 10.8a15 15 0 0 0 6.6 6.6l2.2-2.2a1 1 0 0 1 1-.25 11.4 11.4 0 0 0 3.6.57 1 1 0 0 1 1 1V20a1 1 0 0 1-1 1A17 17 0 0 1 3 4a1 1 0 0 1 1-1h3.5a1 1 0 0 1 1 1c0 1.250.2 2.45.57 3.57a1 1 0 0 1-.25 1z" fill="#e6e6e6"/></svg>
      </span>
      <span class="contacts__text">209-555-0148, 209-555-0172</span>
    </li>
    <li class="contacts__item">
      <span class="contacts__icon">
        <svg width="14" height="18" viewBox="0 0 24 30"><path d="M12 1a9 9 0 0 0-9 9c0 7 9 18 9 18s9-11 9-18a9 9 0 0 0-9-9z" fill="#e6e6e6"/><circle cx="12" cy="10" r="3.5" fill="var(--tiffany)"/></svg>
      </span>
      <span class="contacts__text contacts__text--small">4817 W Falcon Drive Unit 12, Lodi, CA 95240</span>
    </li>
    <li class="contacts__item">
      <span class="contacts__icon">
        <svg width="18" height="13" viewBox="0 0 24 17"><rect x="0" y="0" width="24" height="17" rx="1" fill="#e6e6e6"/><path d="M1 1l11 8 11-8" fill="none" stroke="var(--tiffany)" stroke-width="1.8"/></svg>
      </span>
      <span class="contacts__text">danalistshomes@quillpost.com</span>
    </li>
    <li class="contacts__item">
      <span class="contacts__label">BRE#</span>
      <span>01956027</span>
    </li>
  </ul>

  <div class="agent-photo" role="img" aria-label="Portrait photo of the agent in a dark blazer holding a house key"></div>
  <div class="website-front">www.danalistshomes.com</div>
</section>

<section class="card card--back" aria-label="Business card back">
  <div class="keychain-art" role="img" aria-label="Illustration of a house key on a ring with a house-shaped keychain"></div>
  <svg class="card__lines" width="700" height="400" viewBox="0 0 700 400" aria-hidden="true">
    <line x1="0" y1="100" x2="700" y2="100" stroke="var(--tiffany-light)" stroke-width="2"/>
    <line x1="0" y1="190" x2="700" y2="190" stroke="var(--rule)" stroke-width="1.5"/>
    <line x1="0" y1="252" x2="700" y2="252" stroke="var(--tiffany-light)" stroke-width="2"/>
  </svg>
  <div class="tagline">You pick the door, I find the keys!</div>
  <div class="website-back">WWW.DANALISTSHOMES.COM</div>
</section>

</body>
</html>
```